Landscaping flier 2024

Create a 1 page flier for landscaping services
1. Must be completed in Adobe Photoshop
2. Size 8.5" x 11" (portrait layout)
3. Include logo
4. Text to include:
2024 Gravesite Landscaping Packages
info@hollowbrookmemorial.org
(201) 555-0148
hollowbrookmemorial.org
5. Use chart text for the content. DO NOT COPY THE CHART DESIGN/FORMAT. Use the chart for the text you need only.
6. Use "Pricing cards as format for laying out the chart". Open to other ideas as well.
**Use the example of chart design (handwritten) to base your design off of.
7. Photos
-include before and after care photos

```html
<!DOCTYPE html>
<html lang="en">
<head>
<meta charset="utf-8">
<title>2024 Gravesite Landscaping Packages – Hollowbrook Memorial</title>
<link rel="stylesheet" href="https://fonts.googleapis.com/css2?family=Poppins:wght@400;500;600;700;800&display=swap">
<style>
:root{
  --maroon:#7a2434;
  --maroon-dark:#5e1826;
  --rose:#b88189;
  --pink-row:#e7cfd4;
  --mid-tint:#ecdfe2;
  --grey-row:#eeeded;
  --footer:#363636;
  --ink:#2b2b2b;
  --tick:#3aa64a;
  --cross:#d8323b;
  --gold:#f2b51d;
  --stage:#e9eaea;
}
*{margin:0;padding:0;box-sizing:border-box}
html,body{width:1200px;height:2400px;overflow:hidden;background:var(--stage);font-family:"Poppins",sans-serif;color:var(--ink)}
.flier{position:absolute;left:0;top:424px;width:1200px;height:1552px;background:#fff;overflow:hidden}
.hero-photo{position:absolute;left:420px;top:0;width:780px;height:523px;
  background:linear-gradient(180deg,#c98a52 0%,#c4622c 30%,#a8472a 55%,#6f5a2e 80%,#7f8a4a 100%)}
.title-band{position:absolute;left:0;top:170px;width:900px;height:353px;
  background:linear-gradient(90deg,var(--maroon) 0%,var(--maroon) 62%,rgba(122,36,52,.55) 80%,rgba(122,36,52,0) 100%)}
.logo-panel{position:absolute;left:0;top:0;width:552px;height:170px;background:#fff;border-bottom-right-radius:34px;
  display:flex;align-items:center;justify-content:center;gap:18px;padding-top:38px}
.logo-name{font-weight:500;font-size:34px;color:var(--maroon);letter-spacing:1px;text-transform:uppercase}
.logo-dot{width:40px;height:40px;border-radius:50%;border:3px solid var(--maroon)}
.headline{position:absolute;left:74px;top:208px;color:#fff;line-height:1}
.headline .year{font-weight:700;font-size:140px;letter-spacing:-4px;display:block}
.headline .main{font-weight:800;font-size:71px;display:block;margin-top:-4px}
.headline .sub{font-weight:600;font-size:37px;display:block;margin-top:6px}

.pricing{position:absolute;left:110px;top:506px;width:967px;height:764px;border-radius:18px;overflow:hidden;
  display:grid;grid-template-columns:323px 326px 318px;grid-template-rows:89px 70px 137px 52px 62px 50px 60px 70px 174px;background:var(--grey-row)}
.cell{display:flex;align-items:center;padding-left:32px;font-size:17.5px;font-weight:500;text-transform:uppercase;line-height:1.25}
.cell.mid{background:var(--mid-tint)}
.cell.tint{background:var(--pink-row)}
.cell .ic{flex:0 0 17px;width:17px;height:17px;margin-right:9px;align-self:flex-start;margin-top:3px}
.plan-name{background:var(--maroon);color:#fff;justify-content:center;padding:0;text-align:center;font-weight:600;font-size:27px;line-height:.95}
.plan-desc{background:var(--rose);color:#fff;justify-content:center;padding:0;text-align:center;text-transform:none;font-weight:400;font-size:19px;line-height:1.25}
.feature-detail{display:block;text-transform:none;font-weight:400;font-size:14.5px;margin-top:8px;line-height:1.2}
.weeding{align-items:flex-start;padding-top:22px}
.weeding .center{text-align:center}
.price-cell{flex-direction:column;align-items:center;padding:10px 0 0;text-transform:none;font-weight:400}
.price-cell .trust{align-self:flex-start;padding-left:32px;display:flex;align-items:center;font-weight:500;text-transform:uppercase;font-size:17.5px;margin-bottom:10px}
.price-cell .trust .ic{width:17px;height:17px;margin-right:9px}
.tag{background:var(--maroon);color:#fff;font-size:15px;padding:1px 16px;border-radius:2px}
.amount{font-weight:600;font-size:31px;line-height:1.2}
.note{font-size:16px;text-align:center;line-height:1.2}
.valid{font-size:11px;margin-top:8px}
.terms{display:flex;gap:14px}
.term{display:flex;flex-direction:column;align-items:center}
.term .tag{padding:1px 12px}
.term .amount{font-size:27px}

.badge{position:absolute;left:1042px;top:472px;width:74px;height:74px}
.care-label{position:absolute;top:1297px;height:38px;background:var(--maroon);color:#fff;font-weight:600;font-size:21px;display:flex;align-items:center;justify-content:center}
.care-label.before{left:84px;width:192px;clip-path:polygon(10% 0,100% 0,100% 100%,0 100%)}
.care-label.after{left:924px;width:188px;clip-path:polygon(0 0,100% 0,90% 100%,0 100%)}
.care-photo{position:absolute;top:1276px;width:310px;height:136px;border:3px solid #fff;border-radius:8px;
  background:linear-gradient(180deg,#6f7f5a 0%,#5f9a3a 35%,#6fae3e 70%,#88b84a 100%);z-index:2}
.care-photo.before{left:275px}
.care-photo.after{left:614px}
.footer{position:absolute;left:0;top:1373px;width:1200px;height:179px;background:var(--footer);color:#fff;
  display:flex;align-items:center;justify-content:space-around;padding:38px 40px 0;font-size:25px}
.contact{display:flex;align-items:center;gap:10px}
.contact svg{width:22px;height:22px}
</style>
</head>
<body>
<svg width="0" height="0" style="position:absolute">
  <defs>
    <symbol id="tick" viewBox="0 0 20 20"><circle cx="10" cy="10" r="10" fill="#3aa64a"/><path d="M5.5 10.3l3 3 6-6.3" fill="none" stroke="#fff" stroke-width="2.4" stroke-linecap="round" stroke-linejoin="round"/></symbol>
    <symbol id="cross" viewBox="0 0 20 20"><circle cx="10" cy="10" r="10" fill="#d8323b"/><path d="M6.5 6.5l7 7M13.5 6.5l-7 7" stroke="#fff" stroke-width="2.4" stroke-linecap="round"/></symbol>
  </defs>
</svg>

<main class="flier">
  <div class="hero-photo" role="img" aria-label="Photo of a cemetery lane lined with trees in orange and red autumn foliage"></div>
  <div class="title-band"></div>
  <header class="logo-panel">
    <span class="logo-name">Hollowbrook</span>
    <span class="logo-dot"></span>
    <span class="logo-name">Memorial</span>
  </header>
  <h1 class="headline">
    <span class="year">2024</span>
    <span class="main">GRAVESITE</span>
    <span class="sub">Landscaping Packages</span>
  </h1>

  <section class="pricing">
    <div class="cell plan-name">SEASONAL<br>CARE</div>
    <div class="cell plan-name">BASIC CARE<br>ENDOWMENT</div>
    <div class="cell plan-name">PERPETUAL CARE<br>ENDOWMENT</div>

    <div class="cell plan-desc">Seasonal landscaping<br>grave care.</div>
    <div class="cell plan-desc">Landscaping care forever<br>for graves with no plantings..</div>
    <div class="cell plan-desc">Landscaping care forever<br>for graves with plantings.</div>

    <div class="cell weeding"><svg class="ic"><use href="#tick"/></svg><div>Weeding &amp; trimming<br>on your gravesite<span class="feature-detail">Approximately every 7 weeks during the growing season : mid-April through mid-October</span></div></div>
    <div class="cell weeding mid"><svg class="ic"><use href="#tick"/></svg><div>Weeding &amp; trimming<br>on your gravesite<span class="feature-detail center">2 times per year :<br>mid-May &amp; mid-September</span></div></div>
    <div class="cell weeding"><svg class="ic"><use href="#tick"/></svg><div>Weeding &amp; trimming<br>on your gravesite<span class="feature-detail">Approximately every 7 weeks during the growing season : mid-April through mid-October</span></div></div>

    <div class="cell tint"><svg class="ic"><use href="#cross"/></svg>Monument leveling</div>
    <div class="cell tint"><svg class="ic"><use href="#tick"/></svg>Monument leveling</div>
    <div class="cell tint"><svg class="ic"><use href="#tick"/></svg>Monument leveling</div>

    <div class="cell"><svg class="ic"><use href="#cross"/></svg>Payment ensures<br>grave care forever</div>
    <div class="cell mid"><svg class="ic"><use href="#tick"/></svg>Payment ensures<br>grave care forever</div>
    <div class="cell"><svg class="ic"><use href="#tick"/></svg>Payment ensures<br>grave care forever</div>

    <div class="cell tint"><svg class="ic"><use href="#cross"/></svg>Monument cleaning</div>
    <div class="cell tint"><svg class="ic"><use href="#cross"/></svg>Monument cleaning</div>
    <div class="cell tint"><svg class="ic"><use href="#tick"/></svg>Monument cleaning</div>

    <div class="cell"><svg class="ic"><use href="#cross"/></svg>Full bed of<br>boxwood shrubs</div>
    <div class="cell mid"><svg class="ic"><use href="#cross"/></svg>Full bed of<br>boxwood shrubs</div>
    <div class="cell"><svg class="ic"><use href="#tick"/></svg>Full bed of<br>boxwood shrubs</div>

    <div class="cell tint"><svg class="ic"><use href="#cross"/></svg>Replacement<br>of shrubs</div>
    <div class="cell tint"><svg class="ic"><use href="#cross"/></svg>Replacement<br>of shrubs</div>
    <div class="cell tint"><svg class="ic"><use href="#tick"/></svg>Replacement<br>of shrubs</div>

    <div class="cell price-cell" style="grid-row:span 2">
      <span class="trust"><svg class="ic"><use href="#cross"/></svg>Trust certificate</span>
      <div class="terms">
        <div class="term"><span class="tag">3 Years</span><span class="amount">$396</span></div>
        <div class="term"><span class="tag">2 Years</span><span class="amount">$264</span></div>
        <div class="term"><span class="tag">1 Years</span><span class="amount">$132</span></div>
      </div>
      <span class="note">Multi-year payment locks<br>in current rates</span>
      <span class="valid">Valid through 10/31/2024</span>
    </div>
    <div class="cell price-cell mid" style="grid-row:span 2">
      <span class="trust"><svg class="ic"><use href="#cross"/></svg>Trust certificate</span>
      <span class="tag">12 monthly payments of</span>
      <span class="amount">$287</span>
      <span class="note">Call for single payment discount.</span>
      <span class="valid">Valid through 10/31/2024</span>
    </div>
    <div class="cell price-cell" style="grid-row:span 2">
      <span class="trust"><svg class="ic"><use href="#tick"/></svg>Trust certificate</span>
      <span class="tag">12 monthly payments of</span>
      <span class="amount">$351</span>
      <span class="note">Call for single payment discount.</span>
      <span class="valid">Valid through 10/31/2024</span>
    </div>
  </section>

  <svg class="badge" viewBox="0 0 74 74" aria-label="Most popular">
    <path d="M44 50l10 20 4-8 9 2-10-20z" fill="var(--cross)"/>
    <circle cx="34" cy="34" r="28" fill="var(--gold)"/>
    <circle cx="34" cy="34" r="23" fill="none" stroke="#fff" stroke-width="1.5"/>
    <text x="34" y="31" text-anchor="middle" font-family="Poppins,sans-serif" font-weight="700" font-size="10" fill="var(--maroon)" transform="rotate(-25 34 34)">MOST</text>
    <text x="34" y="43" text-anchor="middle" font-family="Poppins,sans-serif" font-weight="700" font-size="9" fill="var(--maroon)" transform="rotate(-25 34 34)">POPULAR</text>
  </svg>

  <div class="care-label before">BEFORE CARE</div>
  <div class="care-photo before" role="img" aria-label="Before care photo: overgrown gravesite with untrimmed shrubs on grass"></div>
  <div class="care-photo after" role="img" aria-label="After care photo: gravesite with neatly trimmed boxwood shrubs and clean marker"></div>
  <div class="care-label after">AFTER CARE</div>

  <footer class="footer">
    <span class="contact"><svg viewBox="0 0 24 24"><circle cx="12" cy="12" r="12" fill="#fff"/><path d="M8.2 6.5l2 2.4-1.2 1.5c.8 1.7 2 2.9 3.6 3.7l1.5-1.2 2.4 2-1 1.8c-4.2-.3-8-4.1-8.3-8.3z" fill="var(--footer)"/></svg>(201) 555-0148</span>
    <span class="contact"><svg viewBox="0 0 24 24"><circle cx="12" cy="12" r="12" fill="#fff"/><rect x="6" y="8" width="12" height="8.5" rx="1" fill="none" stroke="var(--footer)" stroke-width="1.6"/><path d="M6.5 8.5l5.5 4.3 5.5-4.3" fill="none" stroke="var(--footer)" stroke-width="1.6"/></svg>info@hollowbrookmemorial.org</span>
    <span class="contact"><svg viewBox="0 0 24 24"><circle cx="12" cy="12" r="12" fill="#fff"/><circle cx="12" cy="12" r="6.5" fill="none" stroke="var(--footer)" stroke-width="1.5"/><ellipse cx="12" cy="12" rx="2.8" ry="6.5" fill="none" stroke="var(--footer)" stroke-width="1.3"/><path d="M5.5 12h13" stroke="var(--footer)" stroke-width="1.3"/></svg>www.hollowbrookmemorial.org</span>
  </footer>
</main>
</body>
</html>
```